Church needs a street sign design

We're a small church located in Silicon Valley, California. Our website is https://www.vgtmarlowfield.org/ and our address is 4817 Ferrow Ave, San Jose, California, 95873. You can look up our location on Google Maps to see the sign from Street View. I have uploaded an image of the street sign as well. The marquee, the top section of the sign, and the separating line between them both will be removed. We're seeking a design for a new backlit acrylic insert that will go on the front of the light box and the back of the lightbox. The acrylic sign will fill the entire external frame. In the future, we may build a decorative wood frame around the structural legs, as visualized in one of the uploaded files. The church's brand colors are: #003366 (dark blue), #ff6600 (vibrant orange), #228b22 (forest green). I have also uploaded the church's logo assets. Our primary font is Montserrat and the secondary is Poppins. You can deviate from these colors/fonts if the sign is still coherent with the rest of our branding. Our branding values are mission, truth, passion, and community (please do not put those words on the sign! They are just intended to guide the look of the design). The sign dimensions are 96" by 47.5". Keep in mind that the sign will be backlit on a busy street side. It will also be positioned next to an old-looking church building. We do NOT want a sign that looks traditional, old, or antiquated. Instead, we want a modern-looking sign that pairs well with our old building while helping it look more modern too. We would also like the web address clearly visible on the sign: vgtmarlowfield.org. If you have any questions, just let me know!

```html
<!DOCTYPE html>
<html lang="en">
<head>
<meta charset="utf-8">
<title>Valley Grace Tabernacle – Street Sign</title>
<link href="https://fonts.googleapis.com/css2?family=Montserrat:wght@600&family=Poppins:wght@500;600;700;800&family=Kaushan+Script&display=swap" rel="stylesheet">
<style>
  :root {
    --navy: #03224a;
    --orange: #f2660f;
    --white: #ffffff;
    --ink: #2a2a2a;
    --url-light: #e9edf3;
    --page: #e6e6e6;
  }
  * { margin: 0; padding: 0; box-sizing: border-box; }
  html, body { width: 1200px; height: 904px; overflow: hidden; background: var(--page); }
  .sign {
    position: absolute; left: 30px; top: 170px;
    width: 1140px; height: 564px; overflow: hidden;
    background: var(--white);
  }
  .sign-art { position: absolute; inset: 0; }
  .brand {
    position: absolute; left: 52px; top: 64px;
    font-family: "Montserrat", sans-serif; font-weight: 600;
    font-size: 34px; line-height: 1.1; letter-spacing: 1px;
    color: var(--ink);
    display: flex; align-items: center; gap: 16px;
  }
  .brand-mark { width: 48px; height: 48px; border: 4px solid var(--ink); flex: none; }
  .headline {
    position: absolute; right: 44px; top: 58px;
    font-family: "Poppins", sans-serif; font-weight: 800;
    font-size: 84px; line-height: 72px; text-align: right;
    color: var(--navy); letter-spacing: -1px;
  }
  .subline {
    position: absolute; right: 44px; top: 216px;
    font-family: "Poppins", sans-serif; font-weight: 700;
    font-size: 37px; line-height: 40px; color: var(--ink);
  }
  .tagline {
    position: absolute; left: 486px; width: 627px; top: 284px; height: 72px;
    display: flex; align-items: center; justify-content: center;
    font-family: "Kaushan Script", cursive; font-size: 50px;
    color: var(--white);
  }
  .web {
    position: absolute; left: 400px; width: 680px; top: 448px;
    text-align: center;
    font-family: "Poppins", sans-serif; font-weight: 500;
    font-size: 58px; letter-spacing: 1px; color: var(--url-light);
  }
  .web-name { color: var(--orange); font-weight: 600; }
</style>
</head>
<body>
<div class="sign">
  <svg class="sign-art" width="1140" height="564" viewBox="0 0 1140 564">
    <defs>
      <linearGradient id="cityDusk" x1="0" y1="0" x2="0" y2="1">
        <stop offset="0" stop-color="#b9a58e"/>
        <stop offset="0.35" stop-color="#f2c07c"/>
        <stop offset="0.45" stop-color="#8d8076"/>
        <stop offset="0.7" stop-color="#5b4a34"/>
        <stop offset="1" stop-color="#2e2618"/>
      </linearGradient>
    </defs>
    <rect class="photo-city" x="0" y="0" width="800" height="564" fill="url(#cityDusk)" role="img" aria-label="Aerial photo of a downtown skyline at sunset"/>
    <polygon class="panel-white" fill="var(--white)"
      points="772,0 1140,0 1140,564 269,564 330,480 372,430 392,410 420,378 455,350 500,300 540,250 572,222 600,180 640,140 680,110 710,60 740,40"/>
    <polygon class="brush-band" fill="var(--orange)"
      points="492,284 560,280 700,283 860,279 1000,282 1112,281 1108,300 1116,318 1104,338 1110,356 960,352 800,357 640,353 520,356 498,350 486,330 494,312"/>
    <polygon class="panel-navy" fill="var(--navy)"
      points="445,410 520,404 600,409 700,402 800,408 900,403 1000,408 1080,402 1140,406 1140,564 269,564 330,482 372,432 410,412"/>
  </svg>

  <div class="brand"><span class="brand-mark"></span><span>VALLEY GRACE<br>TABERNACLE</span></div>
  <div class="headline">MAKING<br>DISCIPLES</div>
  <div class="subline">&amp; HELPING THE HELPLESS</div>
  <div class="tagline">For the Glory of Christ</div>
  <div class="web">www.<span class="web-name">vgtmarlowfield</span>.org</div>
</div>
</body>
</html>
```